Business Card Design (NEW FILES)

ATTENTION: New vector files are available. Please update your design to reflect/use the new (better resolution) logo images.

Seeking a unique and professional business card design for a commercial drone photography/videography business. The layout should feature
the logo (attached) and include the following information:
Owen Tarrick
614-502-7738
www.skylarkreelworks.example
NRD Certified Remote Pilot

Owen Tarrick

```html
<!DOCTYPE html>
<html lang="en">
<head>
<meta charset="utf-8">
<title>Skylark Reelworks — Business Card</title>
<link rel="stylesheet" href="https://fonts.googleapis.com/css2?family=Open+Sans:wght@400;600;700&display=swap">
<style>
  :root {
    --stage: #222222;
    --paper: #fffdf4;
    --navy: #1c1f52;
    --navy-deep: #15184a;
    --navy-light: #2c3a9a;
    --orange: #ec8a3f;
    --ghost: #ebe9e3;
    --white: #ffffff;
  }
  * { box-sizing: border-box; margin: 0; padding: 0; }
  html, body { width: 1200px; height: 780px; overflow: hidden; }
  body {
    background: var(--stage);
    font-family: "Open Sans", Arial, sans-serif;
    position: relative;
  }
  .card {
    position: absolute;
    top: 236px;
    width: 540px;
    height: 308px;
    border-radius: 3px;
    overflow: hidden;
    box-shadow: 0 14px 30px rgba(0,0,0,0.45);
  }
  .card--front { left: 40px; background: var(--paper); color: var(--navy); }
  .card--back { left: 620px; background: var(--navy-deep); }

  .drone-art {
    position: absolute;
    border-radius: 50%;
  }
  .card--front .drone-art {
    left: 90px; top: 20px; width: 380px; height: 270px;
    background: radial-gradient(ellipse at center, var(--ghost) 0%, rgba(235,233,227,0.5) 45%, rgba(255,253,244,0) 72%);
  }
  .card--back .drone-art {
    left: 40px; top: 10px; width: 480px; height: 290px;
    background: radial-gradient(ellipse at center, var(--navy-light) 0%, rgba(44,58,154,0.45) 45%, rgba(21,24,74,0) 72%);
  }

  .holder {
    position: absolute;
    left: 60px; top: 70px;
  }
  .holder__name {
    font-size: 30px;
    font-weight: 700;
    letter-spacing: 0.5px;
    line-height: 1.1;
  }
  .holder__first { color: var(--orange); font-weight: 600; }
  .holder__last { color: var(--navy); }
  .holder__role {
    font-size: 15px;
    text-align: right;
    margin-top: 2px;
  }

  .contact {
    position: absolute;
    left: 262px; top: 170px;
    max-width: 258px;
    list-style: none;
    font-size: 15px;
    line-height: 1.55;
    white-space: nowrap;
  }
  .contact__item { display: flex; align-items: center; gap: 8px; }
  .contact__icon { width: 13px; height: 13px; flex: none; }

  .credentials {
    position: absolute;
    left: 36px; top: 224px;
    width: 216px;
    text-align: center;
    font-size: 15px;
    line-height: 1.45;
  }

  .brand {
    position: absolute;
    left: 0; right: 0; top: 132px;
    display: flex; align-items: center; justify-content: center; gap: 10px;
  }
  .brand__name {
    color: var(--white);
    font-size: 26px;
    font-weight: 400;
    letter-spacing: 1.5px;
    text-transform: uppercase;
  }
  .brand__dot {
    width: 14px; height: 14px; border-radius: 50%;
    background: var(--orange);
  }
</style>
</head>
<body>

  <section class="card card--front" aria-label="Business card front">
    <div class="drone-art" role="img" aria-label="Faint drone illustration in the background"></div>

    <div class="holder">
      <h1 class="holder__name"><span class="holder__first">Owen</span> <span class="holder__last">Tarrick</span></h1>
      <p class="holder__role">Owner</p>
    </div>

    <ul class="contact">
      <li class="contact__item">
        <svg class="contact__icon" viewBox="0 0 16 16" aria-hidden="true">
          <path fill="var(--orange)" d="M3.5 1.5l2.5 0 1 3.5-1.8 1.2a8 8 0 0 0 4.6 4.6l1.2-1.8 3.5 1v2.5c0 .8-.7 1.5-1.5 1.5A12 12 0 0 1 2 3c0-.8.7-1.5 1.5-1.5z"/>
        </svg>
        <span>614-502-7738</span>
      </li>
      <li class="contact__item">
        <svg class="contact__icon" viewBox="0 0 16 16" aria-hidden="true">
          <circle cx="8" cy="8" r="6.5" fill="none" stroke="var(--orange)" stroke-width="1.6"/>
          <ellipse cx="8" cy="8" rx="2.8" ry="6.5" fill="none" stroke="var(--orange)" stroke-width="1.2"/>
          <line x1="1.5" y1="8" x2="14.5" y2="8" stroke="var(--orange)" stroke-width="1.2"/>
        </svg>
        <span>www.skylarkreelworks.example</span>
      </li>
    </ul>

    <p class="credentials">NRD Certified Remote Pilot<br>Fully Insured</p>
  </section>

  <section class="card card--back" aria-label="Business card back">
    <div class="drone-art" role="img" aria-label="Large drone illustration in blue tones"></div>
    <div class="brand">
      <span class="brand__name">Skylark Reelworks</span>
      <span class="brand__dot" aria-hidden="true"></span>
    </div>
  </section>

</body>
</html>
```